KORV PTY LTD - Business Cards

Design a modern business card - using the attached Designs.
Same design as on the front, apart from the names/numbers/emails to be different.
We want the cards to be very glossy to stand out, do I think the simple black/white/metallic will be effective.
Both lots of details below:

Tom Wrenshaw
Director
tom_korv@nulvane.com
0438 274 093

Lewis Corbyn
Director
lewis_korv@nulvane.com
0419 385 642

Industry/Entity Type

Business

```html
<!DOCTYPE html>
<html lang="en">
<head>
<meta charset="utf-8">
<title>KORV PTY LTD – Business Cards</title>
<link rel="stylesheet" href="https://fonts.googleapis.com/css2?family=Noto+Serif&family=Open+Sans:wght@400;700&display=swap">
<style>
  :root {
    --backdrop: #e6e4e1;
    --card-dark: #2a3137;
    --card-white: #ffffff;
    --card-grey: #b4b4b4;
    --accent-band: #c9cccc;
    --text-light: #f2f2f2;
    --brand-dark: #2a3137;
    --ghost-mark: #3a4249;
  }
  * { margin: 0; padding: 0; box-sizing: border-box; }
  html, body {
    width: 1200px;
    height: 475px;
    overflow: hidden;
    background: var(--backdrop);
  }
  .sheet {
    position: relative;
    width: 1200px;
    height: 475px;
    display: flex;
    align-items: center;
    justify-content: center;
    gap: 40px;
  }
  .card {
    position: relative;
    width: 540px;
    height: 335px;
    overflow: hidden;
    box-shadow: 0 8px 22px rgba(0, 0, 0, 0.25);
  }
  .card__shapes {
    position: absolute;
    inset: 0;
    width: 100%;
    height: 100%;
  }

  /* Brand name block (replaces the mark) */
  .brand {
    position: absolute;
    display: flex;
    align-items: center;
    font-family: "Open Sans", sans-serif;
    font-weight: 700;
    color: var(--brand-dark);
    white-space: nowrap;
  }
  .brand__dot {
    border-radius: 50%;
    background: var(--brand-dark);
    flex: none;
  }
  .card--front .brand {
    left: 22px;
    top: 152px;
    font-size: 20px;
    gap: 8px;
  }
  .card--front .brand__dot { width: 16px; height: 16px; }

  .card--back { background: var(--card-grey); }
  .card--back .brand {
    left: 50%;
    top: 50%;
    transform: translate(-50%, -50%);
    font-size: 42px;
    gap: 16px;
  }
  .card--back .brand__dot { width: 34px; height: 34px; }

  /* Contact details */
  .contact {
    position: absolute;
    right: 26px;
    top: 0;
    bottom: 0;
    color: var(--text-light);
    text-align: right;
  }
  .contact__name {
    position: absolute;
    right: 0;
    top: 92px;
    font-family: "Noto Serif", serif;
    font-size: 21px;
    white-space: nowrap;
  }
  .contact__role {
    position: absolute;
    right: 0;
    top: 124px;
    font-family: "Noto Serif", serif;
    font-size: 13px;
  }
  .contact__line {
    position: absolute;
    right: 0;
    display: flex;
    align-items: center;
    gap: 6px;
    font-family: "Open Sans", sans-serif;
    font-size: 15px;
    white-space: nowrap;
  }
  .contact__line--phone { top: 188px; }
  .contact__line--email { top: 216px; }
  .contact__icon { width: 12px; height: 12px; fill: var(--text-light); }

  .ghost-name {
    position: absolute;
    right: 30px;
    bottom: 26px;
    font-family: "Open Sans", sans-serif;
    font-weight: 700;
    font-size: 40px;
    color: var(--ghost-mark);
  }
</style>
</head>
<body>
<main class="sheet">

  <section class="card card--front" aria-label="Business card front">
    <svg class="card__shapes" viewBox="0 0 540 335" preserveAspectRatio="none" aria-hidden="true">
      <rect width="540" height="335" fill="var(--card-dark)"/>
      <path d="M300 0 H335 C292 90 258 250 218 335 H190 C230 250 252 80 300 0 Z" fill="var(--accent-band)"/>
      <path d="M0 0 H300 C252 80 230 250 190 335 H0 Z" fill="var(--card-white)"/>
    </svg>

    <div class="brand">
      <span class="brand__dot"></span>
      <span class="brand__name">KORV PTY LTD</span>
    </div>

    <div class="contact">
      <p class="contact__name">Lewis Corbyn</p>
      <p class="contact__role">Director</p>
      <p class="contact__line contact__line--phone">
        <svg class="contact__icon" viewBox="0 0 24 24" aria-hidden="true">
          <path d="M6.6 10.8a15.1 15.1 0 0 0 6.6 6.6l2.2-2.2a1 1 0 0 1 1-.25 11.4 11.4 0 0 0 3.6.57 1 1 0 0 1 1 1V20a1 1 0 0 1-1 1A17 17 0 0 1 3 4a1 1 0 0 1 1-1h3.5a1 1 0 0 1 1 1c0 1.25.2 2.45.57 3.6a1 1 0 0 1-.25 1z"/>
        </svg>
        <span>0419 385 642</span>
      </p>
      <p class="contact__line contact__line--email">
        <svg class="contact__icon" viewBox="0 0 24 24" aria-hidden="true">
          <path d="M2 5h20v14H2z M4 7v.4l8 5 8-5V7z" fill-rule="evenodd"/>
        </svg>
        <span>lewis_korv@nulvane.com</span>
      </p>
    </div>

    <p class="ghost-name" aria-hidden="true">KORV</p>
  </section>

  <section class="card card--back" aria-label="Business card back">
    <div class="brand">
      <span class="brand__dot"></span>
      <span class="brand__name">KORV PTY LTD</span>
    </div>
  </section>

</main>
</body>
</html>
```